Children’s entertainer/balloon artist Website Home Page and custom landing page

I need a home page design for the home page of a children and family entertainer/balloon twister’s website. I also need a custom landing page for family theatre shows performed by the same entertainer.
It will be a Wordpress website and I need the final artwork in a layer Photoshop file with all the layers clearly named and labeled.

Target Market(s)

The site visitors are mainly mums, aged between early 20’s and late 30’s. Other visitors will included companies for Christmas functions, and event organisers for corporate functions.

Industry/Entity Type

Entertainment

Number of Pages Required

2 page

Font styles to use
Sans Serif

Colors
34a6d7
f37122

Requirements
Must have
• Layout
• I have included a wireframe for the home page layout and the custom landing page for your reference. This is a guide only and I welcome your interpretation with the rough layout provided.
• This website needs to look good on all devices as it will be fully responsive.
• It needs to include a footer area on the page, that has social media and a call to action area included.
• Colours
• The main colours for the site is:
• orange (call to action colour)
• ff6800
• blue/turquoise
• 42abc3
• Pictures
• I have included images of the entertainer/balloon artist for you to use/take inspiration from.
• These images will be included on the website. I want to show lots of people having fun.
• I would like to have elements of the logo used in isolation across the website
• i.e. the octopus figure to be included in the footer or the bird element to be included in the testimonial slider etc.
• Elements to include
• Note: use the images of the entertainer in the boxes on the home page (balloon shows, balloon twisting, balloon workshops, theatre shows (the three little balloon pigs on his head)
Nice to have
Should not have
• Element to avoid
• Stock imagery of balloon sculptures - use images provided.

```html
<!DOCTYPE html>
<html lang="en">
<head>
<meta charset="utf-8">
<title>Benny Bloom – Kids Entertainer</title>
<link href="https://fonts.googleapis.com/css2?family=Open+Sans:wght@400;600;700;800&family=Fredoka:wght@600&family=Alfa+Slab+One&display=swap" rel="stylesheet">
<style>
:root{
  --blue:#34a6d7;
  --orange:#f37122;
  --orange-dark:#d95c10;
  --ink:#333;
  --muted:#888;
  --page:#efefef;
  --panel:#f6f6f6;
  --footer:#1f1f1f;
  --footer-text:#bbb;
  --green:#7bc043;
}
*{box-sizing:border-box;margin:0;padding:0}
html,body{width:809px;height:1200px;overflow:hidden}
body{background:radial-gradient(ellipse at 50% 0,#fafafa 0,var(--page) 70%);font-family:"Open Sans",sans-serif;color:var(--ink);position:relative}
.site-header{position:absolute;left:0;top:0;width:809px;height:108px}
.brand{position:absolute;left:22px;top:14px;display:flex;align-items:center;gap:8px}
.brand-mark{width:34px;height:34px;background:var(--orange);border-radius:50%}
.brand-name{font-weight:800;font-size:20px;color:var(--blue);line-height:1}
.booking{position:absolute;right:48px;top:32px;display:flex;align-items:center;gap:6px;font-size:11px;color:var(--muted)}
.booking strong{color:var(--orange);font-size:14px;font-weight:700}
.main-nav{position:absolute;left:350px;top:73px;width:411px;height:27px;display:flex;background:var(--blue)}
.main-nav a{flex:auto;text-align:center;font-size:10.5px;line-height:27px;color:#fff;text-decoration:none;border-right:1px solid rgba(255,255,255,.25)}
.main-nav a.active{background:var(--orange)}
.main-nav a:last-child{border:0}
.hero{position:absolute;left:48px;top:113px;width:713px;height:357px;background:linear-gradient(135deg,#e9eef3 0%,#cfd9e2 40%,#e2a35c 75%,#f0c070 100%);overflow:hidden}
.hero-title{position:absolute;left:52px;top:232px}
.hero-title .small{display:block;font-family:"Fredoka",sans-serif;font-size:36px;color:var(--green);line-height:1}
.hero-title .big{display:block;font-family:"Alfa Slab One",serif;font-size:38px;color:#fff;letter-spacing:1px;line-height:1.1}
.hero-arrow{position:absolute;top:160px;width:24px;height:34px;background:rgba(0,0,0,.35);display:flex;align-items:center;justify-content:center}
.hero-arrow.prev{left:0}.hero-arrow.next{right:0}
.testimonial{position:absolute;left:48px;top:490px;width:465px;height:90px;background:#fff;border:1px solid #ddd;display:flex;align-items:center;gap:14px;padding:0 16px}
.avatar{flex:none;width:52px;height:52px;border-radius:50%;background:linear-gradient(#c9a889,#7a5c48)}
.quote{font-size:8.5px;line-height:1.5;color:#777}
.quote .mark{font-size:22px;color:#555;font-weight:800;line-height:0;vertical-align:-8px;margin-right:3px}
.quote a{color:var(--orange);display:block;margin-top:3px}
.btn{display:inline-flex;align-items:center;justify-content:center;gap:8px;color:#fff;text-decoration:none;font-weight:600;text-transform:uppercase}
.btn-cta{position:absolute;left:567px;top:522px;width:163px;height:34px;background:var(--orange);font-size:11px;letter-spacing:1px;border-radius:2px}
.welcome{position:absolute;left:48px;top:612px;width:470px}
.welcome h1{font-size:22px;font-weight:400;letter-spacing:1px;color:#444;margin-bottom:10px}
.welcome h1 span{color:var(--blue);font-weight:700}
.welcome p{font-size:8.5px;line-height:1.6;color:#777;margin-bottom:10px}
.btn-small{background:var(--blue);height:22px;width:78px;font-size:8px;letter-spacing:1px;border-radius:2px}
.feed{position:absolute;left:540px;top:607px;width:221px;height:226px;background:var(--panel);padding:14px 16px}
.feed h2{font-size:18px;font-weight:400;color:#444;letter-spacing:1px;padding-bottom:10px;border-bottom:1px solid #ddd;margin-bottom:10px}
.feed h2 span{color:var(--blue);font-weight:700}
.feed-item{display:flex;gap:10px;margin-bottom:14px;font-size:8px;line-height:1.5;color:#777}
.feed-item i{flex:none;width:14px;height:14px;border-radius:50%;background:var(--blue);margin-top:2px}
.feed-item b{color:var(--blue);font-weight:400}
.services{position:absolute;left:48px;top:865px;width:713px;display:flex;gap:16px}
.service{position:relative;flex:1;height:212px;overflow:hidden}
.service:nth-child(1){background:linear-gradient(160deg,#5b84b0,#2e3f5b)}
.service:nth-child(2){background:linear-gradient(160deg,#e7a9c0,#c46a87)}
.service:nth-child(3){background:linear-gradient(160deg,#efb25b,#c95e2a)}
.service:nth-child(4){background:linear-gradient(160deg,#9db7cf,#3b5572)}
.service-label{position:absolute;left:0;bottom:0;width:100%;height:50px;background:rgba(0,0,0,.55);text-align:center;color:#fff;padding-top:9px}
.service-label h3{font-size:11px;font-weight:700;letter-spacing:.5px}
.service-label small{display:block;font-size:7px;letter-spacing:1px;margin-top:4px;color:#ddd}
.site-footer{position:absolute;left:0;top:1095px;width:809px;height:105px;background:var(--footer)}
.footer-links{position:absolute;left:48px;top:30px;font-size:9px;color:var(--footer-text)}
.footer-links a{color:var(--footer-text);text-decoration:none}
.copyright{position:absolute;left:48px;top:50px;font-size:8px;color:#888}
.btn-footer{position:absolute;right:48px;top:22px;width:128px;height:28px;background:var(--blue);font-size:10px;letter-spacing:1px}
.social{position:absolute;right:48px;top:60px;display:flex;gap:5px}
.social i{width:16px;height:16px;background:#555}
</style>
</head>
<body>
<header class="site-header">
  <div class="brand"><span class="brand-mark"></span><span class="brand-name">Benny Bloom</span></div>
  <div class="booking">
    <svg width="14" height="14" viewBox="0 0 24 24"><path fill="#888" d="M6.6 10.8a15.1 15.1 0 0 0 6.6 6.6l2.2-2.2a1 1 0 0 1 1-.25 11.4 11.4 0 0 0 3.6.57 1 1 0 0 1 1 1V20a1 1 0 0 1-1 1A17 17 0 0 1 3 4a1 1 0 0 1 1-1h3.5a1 1 0 0 1 1 1c0 1.25.2 2.45.57 3.57a1 1 0 0 1-.25 1z"/></svg>
    Book Now: <strong>1800 555 010</strong>
  </div>
  <nav class="main-nav">
    <a class="active" href="#">Home</a><a href="#">Balloon Shows</a><a href="#">Balloon Twisting</a><a href="#">Theatre</a><a href="#">Reviews</a><a href="#">Contact Us</a>
  </nav>
</header>

<section class="hero" role="img" aria-label="Entertainer in glasses wearing a large balloon hat, surrounded by colourful balloon sculptures">
  <div class="hero-title"><span class="small">kids</span><span class="big">Entertainer</span></div>
  <span class="hero-arrow prev"><svg width="8" height="12" viewBox="0 0 8 12"><path d="M7 1 2 6l5 5" stroke="#fff" stroke-width="2" fill="none"/></svg></span>
  <span class="hero-arrow next"><svg width="8" height="12" viewBox="0 0 8 12"><path d="m1 1 5 5-5 5" stroke="#fff" stroke-width="2" fill="none"/></svg></span>
</section>

<section class="testimonial">
  <div class="avatar" role="img" aria-label="Portrait of a happy parent"></div>
  <p class="quote"><span class="mark">“</span>Lorem ipsum dolor sit amet, consectetur adipiscing elit, sed do eiusmod tempor incididunt ut labore et dolore magna aliqua. Ut enim ad minim veniam, quis nostrud exercitation ullamco laboris nisi ut aliquip ex ea commodo consequat.<a href="#">Jessie Smith</a></p>
</section>
<a class="btn btn-cta" href="#"><svg width="14" height="10" viewBox="0 0 14 10"><rect x=".5" y=".5" width="13" height="9" fill="none" stroke="#fff"/><path d="M.5.5 7 5.5 13.5.5" fill="none" stroke="#fff"/></svg>Get in touch</a>

<section class="welcome">
  <h1>WELCOME TO <span>MY SITE</span></h1>
  <p>Lorem ipsum dolor sit amet, consectetur adipiscing elit, sed do eiusmod tempor incididunt ut labore et dolore magna aliqua. Ut enim ad minim veniam, quis nostrud exercitation ullamco laboris nisi ut aliquip ex ea commodo consequat. Lorem ipsum dolor sit amet, consectetur adipiscing elit.</p>
  <p>Sed do eiusmod tempor incididunt ut labore et dolore magna aliqua. Ut enim ad minim veniam, quis nostrud exercitation ullamco laboris nisi ut aliquip ex ea commodo consequat. Duis aute irure dolor in reprehenderit in voluptate velit esse cillum dolore eu fugiat nulla pariatur, excepteur sint occaecat cupidatat non proident.</p>
  <a class="btn btn-small" href="#">Read more</a>
</section>

<aside class="feed">
  <h2>SOCIAL <span>FEED</span></h2>
  <div class="feed-item"><i></i><p>Lorem <b>@username</b> sit amet, consectetur adipiscing elit, sed do eiusmod.</p></div>
  <div class="feed-item"><i></i><p>Lorem <b>@username</b> sit amet, consectetur adipiscing elit, sed do eiusmod.</p></div>
  <div class="feed-item"><i></i><p>Lorem <b>@username</b> sit amet, consectetur adipiscing elit, sed do eiusmod.</p></div>
</aside>

<section class="services">
  <article class="service" role="img" aria-label="Entertainer performing a balloon show"><div class="service-label"><h3>BALLOON SHOWS</h3><small>READ MORE</small></div></article>
  <article class="service" role="img" aria-label="Pink balloon pig sculpture"><div class="service-label"><h3>BALLOON TWISTING</h3><small>READ MORE</small></div></article>
  <article class="service" role="img" aria-label="Entertainer with colourful balloons at a workshop"><div class="service-label"><h3>BALLOON WORKSHOP</h3><small>READ MORE</small></div></article>
  <article class="service" role="img" aria-label="Entertainer on stage at a theatre show"><div class="service-label"><h3>THEATRE SHOWS</h3><small>READ MORE</small></div></article>
</section>

<footer class="site-footer">
  <div class="footer-links"><a href="#">Home</a> | <a href="#">Balloon Shows</a> | <a href="#">Balloon Twisting</a> | <a href="#">Theatre</a> | <a href="#">Reviews</a> | <a href="#">Contact</a></div>
  <p class="copyright">© Benny Bloom, 2015 All Rights Reserved</p>
  <a class="btn btn-footer" href="#">Contact us</a>
  <div class="social"><i></i><i></i><i></i><i></i></div>
</footer>
</body>
</html>
```